Dental Medical History Form - Content provided

Design a medical history form for a dental practice. Content is provided so all that is needed is the formatting to make it look great and easy to read.

"Patient Information" to include all information contained in top portion of the "Patient Medical History Form" docx file.

"Medical History" should follow the formatting and content of the "Exact Medical History" file as this is what the entry fields look like in our practice software and so we would like it to match.

1st page - Patient info, allergies, medications, antibiotics, joint replacement, pregnancy.

2nd page - Do you have, or have you had, any of the following? . . . . . . .
Updates

Target Market(s)

All ages but must be clear enough for elderly to read. Use as much space as possible to keep font size bigger yet keep to two pages

Industry/Entity Type

Dental

Font styles to use
Sans Serif

Requirements
Must have
• All content provided
• Our logo at the top (file provided)
• Century Gothic Font
• Limit to two pages

```html
<!DOCTYPE html>
<html lang="en">
<head>
<meta charset="utf-8">
<title>Medical History Form – Page 2</title>
<link href="https://fonts.googleapis.com/css2?family=Source+Sans+3:ital,wght@0,400;0,600;0,700;1,400;1,600&display=swap" rel="stylesheet">
<style>
  :root{
    --backdrop:#a9c0dc;
    --paper:#ffffff;
    --ink:#1d2f5e;
    --teal:#2c93b5;
    --teal-light:#6fc3dc;
    --blue-deep:#1f5fa8;
    --box:#86cde2;
  }
  *{box-sizing:border-box;margin:0;padding:0}
  html,body{width:1200px;height:784px;overflow:hidden}
  body{
    background:var(--backdrop);
    font-family:"Source Sans 3",Arial,sans-serif;
    color:var(--ink);
    display:flex;align-items:center;justify-content:center;
  }
  .form-page{
    position:relative;
    width:540px;height:752px;
    background:var(--paper);
    box-shadow:0 6px 18px rgba(40,70,110,.25);
    display:flex;flex-direction:column;
  }
  .question-band{
    height:30px;
    background:linear-gradient(90deg,var(--teal-light),var(--teal));
    color:#fff;
    font-weight:700;font-style:italic;font-size:13px;
    display:flex;align-items:center;justify-content:flex-end;
    padding:0 22px;
  }
  .history-grid{
    flex:1;
    display:grid;grid-template-columns:1fr 1fr;column-gap:34px;
    padding:14px 26px 0 30px;
  }
  .row{
    height:13.5px;
    display:flex;align-items:center;justify-content:space-between;
    font-size:10.5px;line-height:1;
    white-space:nowrap;
  }
  .row.section{font-weight:700;font-size:11px}
  .answers{display:flex;align-items:center;gap:4px;font-size:9.5px}
  .answers span{display:flex;align-items:center;gap:3px}
  .answers span::after{
    content:"";width:9px;height:9px;border:1px solid var(--box);display:inline-block;
  }
  .answers span + span{margin-left:4px}
  .sign-off{
    height:110px;
    padding:0 30px 20px;
    display:flex;flex-direction:column;justify-content:flex-end;
  }
  .sign-lines{display:flex;gap:40px;margin-bottom:14px}
  .sign-field{flex:1;display:flex;align-items:flex-end;gap:8px;
    font-weight:700;font-style:italic;font-size:12px;color:var(--teal)}
  .sign-field.date{flex:0 0 170px}
  .sign-field i{flex:1;border-bottom:1px solid var(--teal);height:1px}
  .thanks{font-size:8.5px;font-style:italic;line-height:1.35}
  .edge-strip{
    height:6px;
    background:linear-gradient(90deg,var(--blue-deep),var(--teal-light) 40%,#fff 70%);
  }
</style>
</head>
<body>
<main class="form-page">
  <header class="question-band">Do you have, or have you had, any of the following?</header>

  <section class="history-grid">
    <div class="history-column">
      <div class="row section">Dental</div>
      <div class="row">Acid Reflux<div class="answers"><span>Yes</span><span>No</span></div></div>
      <div class="row">Bad Breath/Taste<div class="answers"><span>Yes</span><span>No</span></div></div>
      <div class="row">Bleeding/Swollen/Sore Gums<div class="answers"><span>Yes</span><span>No</span></div></div>
      <div class="row">Blisters/Ulcers in Mouth<div class="answers"><span>Yes</span><span>No</span></div></div>
      <div class="row">Broken teeth/filling<div class="answers"><span>Yes</span><span>No</span></div></div>
      <div class="row">Burning tongue<div class="answers"><span>Yes</span><span>No</span></div></div>
      <div class="row">Dry mouth<div class="answers"><span>Yes</span><span>No</span></div></div>
      <div class="row">Food collection between teeth<div class="answers"><span>Yes</span><span>No</span></div></div>
      <div class="row">Grinding/clenching teeth (day/night)<div class="answers"><span>Yes</span><span>No</span></div></div>
      <div class="row">Loose teeth<div class="answers"><span>Yes</span><span>No</span></div></div>
      <div class="row">Crooked teeth<div class="answers"><span>Yes</span><span>No</span></div></div>
      <div class="row">Discoloured teeth<div class="answers"><span>Yes</span><span>No</span></div></div>
      <div class="row">Sensitivity to Hot/Cold<div class="answers"><span>Yes</span><span>No</span></div></div>
      <div class="row">Tooth pain when chewing<div class="answers"><span>Yes</span><span>No</span></div></div>
      <div class="row">Jaw pain/Fracture<div class="answers"><span>Yes</span><span>No</span></div></div>
      <div class="row">Orthodontic treatment/history<div class="answers"><span>Yes</span><span>No</span></div></div>
      <div class="row">Oral Cancer<div class="answers"><span>Yes</span><span>No</span></div></div>
      <div class="row section">Diet/Lifestyle</div>
      <div class="row">Drink more than one glass alcohol per day<div class="answers"><span>Yes</span><span>No</span></div></div>
      <div class="row">Smoking<div class="answers"><span>Yes</span><span>No</span></div></div>
      <div class="row">Carbonated drinks<div class="answers"><span>Yes</span><span>No</span></div></div>
      <div class="row">Sugary foods<div class="answers"><span>Yes</span><span>No</span></div></div>
      <div class="row section">Blood</div>
      <div class="row">Anaemia<div class="answers"><span>Yes</span><span>No</span></div></div>
      <div class="row">Blood Clots<div class="answers"><span>Yes</span><span>No</span></div></div>
      <div class="row">Leukemia<div class="answers"><span>Yes</span><span>No</span></div></div>
      <div class="row">Low platelets<div class="answers"><span>Yes</span><span>No</span></div></div>
      <div class="row">Lymphoma<div class="answers"><span>Yes</span><span>No</span></div></div>
      <div class="row">Haemophelia<div class="answers"><span>Yes</span><span>No</span></div></div>
      <div class="row section">Chest</div>
      <div class="row">Bronchitis<div class="answers"><span>Yes</span><span>No</span></div></div>
      <div class="row">Cystic Fibrosis<div class="answers"><span>Yes</span><span>No</span></div></div>
      <div class="row">Emphysema<div class="answers"><span>Yes</span><span>No</span></div></div>
      <div class="row">Pneumonia<div class="answers"><span>Yes</span><span>No</span></div></div>
      <div class="row section">Infectious Disease</div>
      <div class="row">Creutzfeldt-Jakob Disease<div class="answers"><span>Yes</span><span>No</span></div></div>
      <div class="row">Hepatitis A,B,C,D<div class="answers"><span>Yes</span><span>No</span></div></div>
    </div>

    <div class="history-column">
      <div class="row">HIV/AIDS<div class="answers"><span>Yes</span><span>No</span></div></div>
      <div class="row">Influenza<div class="answers"><span>Yes</span><span>No</span></div></div>
      <div class="row">Shingles<div class="answers"><span>Yes</span><span>No</span></div></div>
      <div class="row">Tuberculosis<div class="answers"><span>Yes</span><span>No</span></div></div>
      <div class="row section">Heart</div>
      <div class="row">Angina<div class="answers"><span>Yes</span><span>No</span></div></div>
      <div class="row">Atrial Fibrillation<div class="answers"><span>Yes</span><span>No</span></div></div>
      <div class="row">Blood Pressure (High/Low)<div class="answers"><span>Yes</span><span>No</span></div></div>
      <div class="row">Congenital Heart Disease<div class="answers"><span>Yes</span><span>No</span></div></div>
      <div class="row">Heart attack<div class="answers"><span>Yes</span><span>No</span></div></div>
      <div class="row">Heart murmur<div class="answers"><span>Yes</span><span>No</span></div></div>
      <div class="row">Heart surgery<div class="answers"><span>Yes</span><span>No</span></div></div>
      <div class="row">Heart valve replacement<div class="answers"><span>Yes</span><span>No</span></div></div>
      <div class="row">Infective endocarditis<div class="answers"><span>Yes</span><span>No</span></div></div>
      <div class="row">Rheumatic Heart Disease<div class="answers"><span>Yes</span><span>No</span></div></div>
      <div class="row">Pacemaker<div class="answers"><span>Yes</span><span>No</span></div></div>
      <div class="row">Stent<div class="answers"><span>Yes</span><span>No</span></div></div>
      <div class="row section">Other</div>
      <div class="row">Anxiety/PTSD<div class="answers"><span>Yes</span><span>No</span></div></div>
      <div class="row">Arthritis<div class="answers"><span>Yes</span><span>No</span></div></div>
      <div class="row">Alzheimer’s<div class="answers"><span>Yes</span><span>No</span></div></div>
      <div class="row">Asthma<div class="answers"><span>Yes</span><span>No</span></div></div>
      <div class="row">Anaphylaxis<div class="answers"><span>Yes</span><span>No</span></div></div>
      <div class="row">Auto-immune disease<div class="answers"><span>Yes</span><span>No</span></div></div>
      <div class="row">Coeliac<div class="answers"><span>Yes</span><span>No</span></div></div>
      <div class="row">Depression<div class="answers"><span>Yes</span><span>No</span></div></div>
      <div class="row">Diabetes<div class="answers"><span>Yes</span><span>No</span></div></div>
      <div class="row">Epilepsy<div class="answers"><span>Yes</span><span>No</span></div></div>
      <div class="row">Kidney Disease<div class="answers"><span>Yes</span><span>No</span></div></div>
      <div class="row">Liver Disease<div class="answers"><span>Yes</span><span>No</span></div></div>
      <div class="row">Osteoporosis<div class="answers"><span>Yes</span><span>No</span></div></div>
      <div class="row">Parkinson’s<div class="answers"><span>Yes</span><span>No</span></div></div>
      <div class="row">Radiation to Head/Neck<div class="answers"><span>Yes</span><span>No</span></div></div>
      <div class="row">Schizophrenia<div class="answers"><span>Yes</span><span>No</span></div></div>
      <div class="row">Snoring<div class="answers"><span>Yes</span><span>No</span></div></div>
      <div class="row">Sleep apnea<div class="answers"><span>Yes</span><span>No</span></div></div>
      <div class="row">Stroke<div class="answers"><span>Yes</span><span>No</span></div></div>
    </div>
  </section>

  <footer class="sign-off">
    <div class="sign-lines">
      <div class="sign-field date">Date<i></i></div>
      <div class="sign-field">Signature<i></i></div>
    </div>
    <p class="thanks">Thank you for taking the time to complete your medical history form.<br>
    Oral health is linked to overall health and this comprehensive questionnaire will help us to provide you with optimal and safe care.</p>
  </footer>
  <div class="edge-strip"></div>
</main>
</body>
</html>
```